Business Card Design Project

After recently finishing a design project for the company logo using markbazaar, it's now time for a business card. Attached to this is the logo.

The requirements for the business card are pretty straightforward:

- A clean, uncomplicated look
- Consistent usage of fonts
- Designs for both single sided and double sided cards
- A modern layout with preferably space to refer to social media accounts and/or downloadable vcards through a qr code
- consistent application of the company colour scheme: red/white. Hex codes for exact colour can be provided

Thanks!

```html
<!DOCTYPE html>
<html lang="en">
<head>
<meta charset="UTF-8">
<title>Clay Row Recruiting – Business Card</title>
<link href="https://fonts.googleapis.com/css2?family=Open+Sans:ital,wght@0,400;0,600;0,700;1,700&display=swap" rel="stylesheet">
<style>
  :root {
    --brand-red: #e31e2a;
    --ink: #231f20;
    --ink-soft: #3a3a3a;
    --divider: #b5b5b5;
    --card: #ffffff;
    --backdrop: #ebe8e4;
  }
  * { margin: 0; padding: 0; box-sizing: border-box; }
  html, body {
    width: 960px; height: 1200px; overflow: hidden;
    background: var(--backdrop);
    font-family: "Open Sans", Arial, sans-serif;
    color: var(--ink);
  }
  .canvas { position: relative; width: 960px; height: 1200px; }

  .card {
    position: absolute;
    width: 840px; height: 480px;
    background: var(--card);
    border-radius: 30px;
    overflow: hidden;
    box-shadow: 0 1px 3px rgba(0,0,0,0.12);
  }
  .card--front { left: 58px; top: 105px; }
  .card--back  { left: 60px; top: 637px; }

  .brand { position: absolute; display: flex; align-items: center; gap: 22px; }
  .brand__mark { width: 44px; height: 44px; background: var(--brand-red); flex: none; }
  .brand__name {
    font-weight: 600; color: var(--ink);
    line-height: 1.02; letter-spacing: -0.5px;
  }
  .card--front .brand { left: 34px; top: 128px; }
  .card--front .brand__name { font-size: 54px; }
  .card--back .brand { left: 0; right: 0; top: 168px; justify-content: center; }
  .card--back .brand__name { font-size: 62px; }

  .divider {
    position: absolute; left: 528px; top: 103px;
    width: 2px; height: 210px; background: var(--divider);
  }

  .contact { position: absolute; left: 552px; top: 140px; color: var(--ink-soft); }
  .contact__name { font-size: 25px; font-weight: 700; line-height: 1.2; }
  .contact__role { font-size: 20px; line-height: 1.4; margin-bottom: 14px; }
  .contact__line { font-size: 20px; line-height: 30px; }
  .contact__label { font-weight: 700; font-style: italic; color: var(--ink); }

  .footer-band {
    position: absolute; left: 0; right: 0; bottom: 0;
    height: 110px;
    background: var(--brand-red);
  }

  .address {
    position: absolute; left: 42px; top: 400px;
    color: #fff; font-size: 22px; line-height: 34px;
  }
</style>
</head>
<body>
<main class="canvas">

  <section class="card card--front" aria-label="Card front">
    <div class="footer-band" role="img" aria-label="Red decorative wave band along the bottom edge"></div>

    <div class="brand">
      <span class="brand__mark"></span>
      <span class="brand__name">Clay Row<br>Recruiting</span>
    </div>

    <div class="divider"></div>

    <div class="contact">
      <p class="contact__name">Your Name</p>
      <p class="contact__role">Designation</p>
      <p class="contact__line"><span class="contact__label">t</span> : 123-123-1234</p>
      <p class="contact__line"><span class="contact__label">e</span> : info@yourwebsite.com</p>
      <p class="contact__line"><span class="contact__label">w</span> : www.clayrow.com</p>
    </div>

    <p class="address">1234, Street Name, District<br>City, Country Code.</p>
  </section>

  <section class="card card--back" aria-label="Card back">
    <div class="brand">
      <span class="brand__mark"></span>
      <span class="brand__name">Clay Row<br>Recruiting</span>
    </div>
  </section>

</main>
</body>
</html>
```